hello! I need a very simple modern business card for a new venture called The Quiet Harbour Retreats. It's the very first Tech-Free retreat in Asia!

The concept is very unique. Basically a group of 12-15 people would go on a 3 to 4 days retreat where no phone or internet is allowed. The first retreat will take place in a beautiful villa in Bali by the sea. It will include yoga, meditation, art & writing workshops, swimming, hiking, cooking, healthy vegetarian meals, etc.

Reason: Thanks for your submissions. I still haven't found exactly what I'm after but the designs that haven't be eliminated are getting close.. Please keep in mind that it should be a simple, modern and upmarket business card. Thanks

Target Market(s)

Both men and women who would like to disconnect from life, computer and phone for 3/4 days. They can be either local or expats but based in Asia (Singapore, Hong Kong).
Client will have to pay for their own flight and then the price is around US$600 for a 3-day retreat including everything (accommodation, food, activities). It means clients already have a good income. They are usually working in marketing, advertising, digital media, public relations.

Industry/Entity Type

Internet

Font styles to use
Other font styles liked:
• anything modern you like

Colors
acd036
9bcb3c
f37022
f68d4d
1b1b1b
333333
acd037

Requirements
Must have
• Name: Rell Vonta
Position: #screenwanderer
Company: The Quiet Harbour Retreats (asia should be smaller than the rest)
- Email button - quietharbourretreats@mailora.com
- Facebook button - www.pagenook.com/quietharbourretreats
- Eventbrite button - www.quietharbourretreats.ticketvale.com
Nice to have
• You can use my logo attached but it's something I designed quickly on Power Point so it would be nice to include your own version.
Should not have
• anything tacky or girly or childish. thanks

```html
<!DOCTYPE html>
<html lang="en">
<head>
<meta charset="utf-8">
<title>The Quiet Harbour Retreats – Business Card</title>
<link href="https://fonts.googleapis.com/css2?family=Questrial&display=swap" rel="stylesheet">
<style>
  :root {
    --lime: #acd036;
    --lime-deep: #9bcb3c;
    --orange: #f37022;
    --charcoal: #333333;
    --ink: #1b1b1b;
    --backdrop: #f7f7f7;
  }
  * { margin: 0; padding: 0; box-sizing: border-box; }
  html, body {
    width: 1200px; height: 1000px; overflow: hidden;
    background: var(--backdrop);
    font-family: "Questrial", "Century Gothic", sans-serif;
  }
  .sheet { position: relative; width: 1200px; height: 1000px; }

  .card { position: absolute; left: 200px; width: 800px; }
  .card-front { top: 20px; height: 458px; background: var(--orange); }
  .card-back { top: 502px; height: 457px; background: var(--charcoal); }

  .brand {
    position: absolute; left: 118px; top: 160px; height: 140px;
    display: flex; align-items: center; gap: 14px;
  }
  .brand-dot {
    width: 136px; height: 136px; border-radius: 50%;
    background: var(--lime-deep);
  }
  .brand-name {
    color: var(--lime); font-size: 34px; letter-spacing: 1px; word-spacing: 6px;
    white-space: nowrap;
  }

  .web-band {
    position: absolute; left: 0; bottom: 0; width: 100%; height: 41px;
    background: var(--charcoal);
    display: flex; align-items: center; justify-content: center;
  }
  .web-address { color: var(--orange); font-size: 22px; letter-spacing: 1.5px; }

  .person { position: absolute; left: 28px; top: 170px; color: var(--lime); }
  .person-name { font-size: 62px; letter-spacing: 2px; word-spacing: 12px; line-height: 66px; }
  .person-title { font-size: 40px; font-weight: 700; letter-spacing: 0.5px; line-height: 46px; -webkit-text-stroke: 0.8px var(--lime); }

  .divider {
    position: absolute; left: 398px; top: 70px; width: 4px; height: 315px;
    background: linear-gradient(to bottom, rgba(27,27,27,0), var(--ink) 30%, var(--ink) 70%, rgba(27,27,27,0));
  }

  .contacts { position: absolute; left: 422px; top: 162px; list-style: none; }
  .contact { display: flex; align-items: center; gap: 12px; height: 32px; margin-bottom: 15.5px; }
  .contact-icon { width: 32px; height: 32px; flex: none; }
  .contact-square { width: 32px; height: 32px; border-radius: 4px; background: var(--lime); flex: none; }
  .contact-text { color: var(--lime); font-size: 14.5px; letter-spacing: 0.6px; white-space: nowrap; }
</style>
</head>
<body>
<main class="sheet">
  <section class="card card-front">
    <div class="brand">
      <span class="brand-dot"></span>
      <span class="brand-name">The Quiet Harbour Retreats</span>
    </div>
    <div class="web-band"><span class="web-address">www.quietharbourretreats.com</span></div>
  </section>

  <section class="card card-back">
    <div class="person">
      <p class="person-name">Rell Vonta</p>
      <p class="person-title">#screenwanderer</p>
    </div>
    <div class="divider"></div>
    <ul class="contacts">
      <li class="contact">
        <svg class="contact-icon" viewBox="0 0 32 32" aria-hidden="true">
          <rect x="1" y="6" width="30" height="20" fill="var(--lime)"/>
          <path d="M2 7 L16 18 L30 7" fill="none" stroke="var(--charcoal)" stroke-width="2.5"/>
          <path d="M2 25 L12 15 M30 25 L20 15" fill="none" stroke="var(--charcoal)" stroke-width="2"/>
        </svg>
        <span class="contact-text">quietharbourretreats@mailora.com</span>
      </li>
      <li class="contact">
        <span class="contact-square"></span>
        <span class="contact-text">www.pagenook.com/quietharbourretreats</span>
      </li>
      <li class="contact">
        <span class="contact-square"></span>
        <span class="contact-text">www.quietharbourretreats.ticketvale.com</span>
      </li>
    </ul>
  </section>
</main>
</body>
</html>
```